Brell Stone Company Business Cards

Front and Back Business Card - logo and text setup - cool design. I need workable photoshop or illustrator files so I can setup each employee card with design that is created
Updates

Hi everyone, thank you for the great entries. Please no more white and blue cards - there are so many already - black and silver only now please. thanks!

Target Market(s)

Construction Industry - Facility Managers

Industry/Entity Type

Construction

Contact Information for Business Card

I really like contemporary simplistic looks - clean neat....not opposed to seeing some black backrounds

Requirements
Must have
• Logo/website address with design on front only - www.brellstone-example.com (logo attached)
• Back:
• Name/Title/Company Address/Phone/email address
Nice to have
• Cool design
Should not have
• Nothing gimmicky like Fire or Water - since we are a Fire Protection company - it has all been done

```html
<!DOCTYPE html>
<html lang="en">
<head>
<meta charset="utf-8">
<title>Brell Stone Company – Business Card</title>
<link href="https://fonts.googleapis.com/css2?family=Lato:wght@700&family=Roboto:wght@400;700&display=swap" rel="stylesheet">
<style>
  :root {
    --page: #ffffff;
    --card-light: #3b4041;
    --card-dark: #0b0c0c;
    --silver-soft: rgba(120, 132, 132, 0.28);
    --silver-faint: rgba(90, 100, 100, 0.12);
    --brand-red: #f03a24;
    --brand-blue: #1d3c9e;
    --icon-blue: #1f44b8;
  }
  html, body {
    margin: 0;
    padding: 0;
    width: 1200px;
    height: 1200px;
    overflow: hidden;
    background: var(--page);
  }
  .canvas {
    position: relative;
    width: 1200px;
    height: 1200px;
  }
  .card {
    position: absolute;
    left: 150px;
    width: 900px;
    height: 540px;
    overflow: hidden;
    background: linear-gradient(90deg, var(--card-light) 0%, #1c1f20 22%, var(--card-dark) 60%, var(--card-dark) 100%);
  }
  .card--front { top: 53px; }
  .card--back  { top: 613px; }

  .card__texture {
    position: absolute;
    inset: 0;
  }
  .card--front .card__texture {
    background:
      radial-gradient(ellipse 380px 300px at 740px 270px, var(--silver-soft), transparent 70%),
      radial-gradient(ellipse 260px 220px at 860px 80px, var(--silver-faint), transparent 70%);
  }
  .card--back .card__texture {
    background:
      radial-gradient(ellipse 320px 280px at 200px 300px, var(--silver-soft), transparent 70%),
      radial-gradient(ellipse 260px 200px at 400px 60px, var(--silver-faint), transparent 70%);
  }

  .brand-name {
    position: absolute;
    left: 277px;
    top: 262px;
    margin: 0;
    font-family: "Roboto", sans-serif;
    font-weight: 700;
    font-size: 68px;
    line-height: 1;
    color: var(--brand-red);
    letter-spacing: -1px;
  }
  .card--front .brand-name { left: 127px; }
  .brand-url {
    position: absolute;
    left: 128px;
    top: 338px;
    margin: 0;
    font-family: "Roboto", sans-serif;
    font-weight: 400;
    font-size: 18px;
    letter-spacing: 4px;
    color: var(--brand-red);
  }
  .person-name {
    position: absolute;
    left: 458px;
    top: 90px;
    margin: 0;
    font-family: "Lato", sans-serif;
    font-weight: 700;
    font-size: 39px;
    line-height: 1;
    color: var(--brand-red);
  }
  .person-title {
    position: absolute;
    left: 459px;
    top: 138px;
    margin: 0;
    font-family: "Roboto", sans-serif;
    font-weight: 400;
    font-size: 24px;
    line-height: 1;
    color: var(--brand-blue);
  }
  .contact-bracket {
    position: absolute;
    left: 461px;
    top: 235px;
    width: 62px;
    height: 196px;
  }
  .contact-list {
    position: absolute;
    left: 462px;
    top: 267px;
    margin: 0;
    padding: 0;
    list-style: none;
  }
  .contact-list li {
    display: flex;
    align-items: center;
    height: 52px;
    font-family: "Roboto", sans-serif;
    font-weight: 400;
    font-size: 23px;
    color: var(--brand-red);
  }
  .contact-list svg {
    width: 28px;
    height: 28px;
    margin-left: 16px;
    margin-right: 26px;
    fill: var(--icon-blue);
    flex: none;
  }
</style>
</head>
<body>
<div class="canvas">

  <section class="card card--front">
    <div class="card__texture" role="img" aria-label="Background texture of overlapping diagonal brushed-silver bars"></div>
    <h1 class="brand-name">brellstone</h1>
    <p class="brand-url">www.brellstone-example.com</p>
  </section>

  <section class="card card--back">
    <div class="card__texture" role="img" aria-label="Background texture of overlapping diagonal brushed-silver bars"></div>

    <h2 class="person-name">Dana Whitfield</h2>
    <p class="person-title">Managing Director</p>

    <svg class="contact-bracket" viewBox="0 0 62 196" aria-hidden="true">
      <defs>
        <linearGradient id="bracketShine" x1="0" y1="0" x2="0" y2="1">
          <stop offset="0" stop-color="#2a2d2e"/>
          <stop offset="0.5" stop-color="#e6ecec"/>
          <stop offset="1" stop-color="#2a2d2e"/>
        </linearGradient>
      </defs>
      <rect x="1" y="1" width="60" height="194" fill="#0d0f0f" stroke="#1e2223"/>
      <rect x="1" y="0" width="2" height="196" fill="url(#bracketShine)"/>
      <rect x="59" y="0" width="2" height="196" fill="url(#bracketShine)"/>
    </svg>

    <ul class="contact-list">
      <li>
        <svg viewBox="0 0 24 24" aria-hidden="true"><path d="M6.6 10.8a15.2 15.2 0 0 0 6.6 6.6l2.2-2.2a1 1 0 0 1 1-.25 11.4 11.4 0 0 0 3.6.57 1 1 0 0 1 1 1V20a1 1 0 0 1-1 1A17 17 0 0 1 3 4a1 1 0 0 1 1-1h3.5a1 1 0 0 1 1 1c0 1.25.2 2.45.57 3.570a1 1 0 0 1-.25 1z"/></svg>
        (555)-0142-886
      </li>
      <li>
        <svg viewBox="0 0 24 24" aria-hidden="true"><path d="M2 5h20v2l-10 6L2 7z"/><path d="M2 9l10 6 10-6v10H2z"/></svg>
        hello@brellstone-example.com
      </li>
      <li>
        <svg viewBox="0 0 24 24" aria-hidden="true"><path d="M12 2a7 7 0 0 0-7 7c0 5.2 7 13 7 13s7-7.8 7-13a7 7 0 0 0-7-7zm0 9.5A2.5 2.5 0 1 1 12 6.5a2.5 2.5 0 0 1 0 5z"/></svg>
        48 Harbor Ridge Road,USA
      </li>
    </ul>
  </section>

</div>
</body>
</html>
```